Redesign Craft Brewing Recipe Website

Originally built with Bootstrap just to get the site going, I am seeking a complete redesign of the sites home page and recipe page. I am an experienced web developer with no graphic background, initially just looking for psd mocks.

I prefer styles that are clean and modern, and would prefer anything that is fun, engaging, and has an organic feel to it. I currently have a cartoon rabbit as a logo, but it needs some modification/tweaking, so any help in that area would be great as well.

Current site:
http://velvetfinch.cloudpagehost.net/

Current launch page/logo:
http://www.velvetfinch.com/

I like the overall layout of the elements currently, but the design sucks.

The launch page is at the following URL

Reason: Still looking for a more modern design. Designs received so far are too similar to the original.

My site is content based and does not contain images or products. Your design should not consist of large images.

Reason: The website has very little images, so the designs need to be more text and content based. The header needs to be very small and should not contain an ad rotater.

Target Market(s)

Home brewers, Craft brewers, Microbreweries, Brewpubs

Requirements
Must have
• Web 2.0 Look and Feel, Fun, Hip, Focus on content
Should not have
• A large photo as a header

```html
<!DOCTYPE html>
<html lang="en">
<head>
<meta charset="utf-8">
<title>Velvetfinch — Craft Beer Recipes</title>
<link href="https://fonts.googleapis.com/css2?family=Arimo:wght@400;700&display=swap" rel="stylesheet">
<style>
:root{
  --navy:#1e3048;
  --blue-top:#3f7fc4;
  --blue-bot:#1d4f8c;
  --page:#f2f2f2;
  --white:#fff;
  --line:#d6d6d6;
  --text:#444;
  --muted:#666;
  --link:#1f5fa6;
  --panel-top:#4a8fd6;
  --panel-bot:#2463a8;
  --green:#2e9a1a;
  --green-dark:#1f7c0f;
  --orange:#f08a1c;
  --dark:#3d3d3d;
  --stat:#fafafa;
  --srm:#e88a10;
  --ribbon:#6aa915;
}
*{box-sizing:border-box;margin:0;padding:0}
html,body{width:920px;height:1200px;overflow:hidden}
body{font-family:"Arimo",Arial,sans-serif;background:var(--page);color:var(--text);position:relative}
.topbar{position:absolute;left:0;top:0;width:920px;height:57px;background:var(--navy);border-bottom:1px solid #0f1c2c}
.brand{position:absolute;left:68px;top:13px;font-weight:700;font-size:28px;color:var(--white);letter-spacing:.3px}
.social{position:absolute;right:68px;top:21px;display:flex;gap:8px}
.social span{display:inline-flex;gap:3px}
.social b,.social i{font-style:normal;font-size:8px;font-weight:700;background:var(--white);border:1px solid #b9c3d1;border-radius:2px;padding:2px 4px;color:#3b5b8c}
.social i{font-weight:400;color:#333}
.hero{position:absolute;left:0;top:57px;width:920px;height:185px;background:linear-gradient(var(--blue-top),var(--blue-bot))}
.hero-art{position:absolute;left:70px;top:21px;width:82px;height:87px;border-radius:8px 18px 10px 10px;background:linear-gradient(90deg,#e8a326,#f8d066 55%,#d7d7d7)}
.hero h1{position:absolute;left:175px;top:26px;font-weight:400;font-size:15.5px;color:var(--white)}
.hero p{position:absolute;left:175px;top:52px;width:676px;font-size:10.5px;line-height:17.6px;color:#e2ecf8}
.sheet{position:absolute;left:69px;top:194px;width:782px;height:949px;background:var(--white)}
.search{position:absolute;left:13px;top:11px;width:238px;height:28px;border:1px solid var(--line);display:flex}
.search span{flex:1;font-size:8px;color:#666;padding:10px 9px}
.search button{width:37px;margin:1px;border:1px solid #c8c8c8;background:linear-gradient(#e6e6e6,#cfcfcf);font:400 13px "Arimo",sans-serif;color:#555}
.panel{position:absolute;left:13px;width:238px;border:1px solid var(--line)}
.panel h2{height:30px;background:linear-gradient(var(--panel-top),var(--panel-bot));color:var(--white);font-size:14px;font-weight:400;padding:7px 14px;margin:-1px -1px 0;border:1px solid #1b528f}
.panel ul{list-style:none;padding:14px 16px}
.panel li{font-size:11px;height:25.6px;display:flex;align-items:center;gap:9px;color:#333}
.panel li::before{content:"";width:8px;height:8px;border:1px solid #999;background:#eee}
.brewing{top:62px;height:129px}
.styles{top:199px;height:260px}
.styles ul{padding-top:16px}
.scroll{position:absolute;right:13px;top:48px;width:10px;height:198px;background:#f1f1f1;border:1px solid #ddd}
.scroll .knob{position:absolute;left:-2px;top:89px;width:12px;height:12px;border-radius:50%;background:#ddd;border:1px solid #bbb}
.match{top:467px;height:129px}
.tabs{position:absolute;left:267px;top:8px;height:40px;display:flex}
.tab{width:93px;padding-top:13px;text-align:center;font-size:13.5px;color:#333}
.tab.active{background:var(--page);color:var(--link);border-top:1px solid #e2e2e2}
.tab+.tab{width:auto;padding-left:29px}
.feedback{position:absolute;left:702px;top:0;width:70px;height:44px;background:var(--ribbon);color:var(--white);font-weight:700;font-size:11.5px;text-align:center;padding-top:14px;clip-path:polygon(0 0,100% 0,100% 100%,50% 86%,0 100%)}
.feed{position:absolute;left:267px;top:48px;width:507px;height:889px;background:var(--page);padding:15px 15px 0}
.card{height:166px;margin-bottom:8px;background:var(--white);border:2px solid #e4e4e4;box-shadow:0 0 0 1px #d0d0d0 inset;padding:13px 11px}
.card h3{font-weight:400;font-size:13.5px;color:var(--link);margin:0 0 0 2px}
.card p{font-size:9.5px;line-height:14.4px;color:var(--muted);margin:6px 0 0 2px}
.meta{height:35px;margin-top:11px;background:var(--page);display:flex;align-items:center;padding-left:15px;font-size:9.5px;color:#555}
.meta .by{width:150px;border-right:1px solid #ddd;height:27px;display:flex;align-items:center}
.meta .by a{color:var(--link);text-decoration:none;margin-left:5px}
.tag{color:var(--white);font-size:11px;padding:4px 10px;border-radius:2px;margin-left:14px}
.tag+.tag{margin-left:11px}
.tag.extract{background:linear-gradient(#3bb024,var(--green-dark))}
.tag.mash{background:linear-gradient(#f6a040,#e27b10)}
.tag.style{background:linear-gradient(#555,#2f2f2f)}
.stats{display:flex;gap:4px;margin-top:6px}
.stat{flex:1;height:37px;border:1px solid #d3d3d3;border-radius:3px;background:var(--stat);box-shadow:0 1px 0 #ccc;text-align:center;padding-top:5px}
.stat strong{display:block;font-size:12px;color:#555}
.stat span{font-size:9.5px;color:#666}
.stat.srm strong,.stat.srm span{color:var(--srm)}
.footer{position:absolute;left:0;top:1153px;width:920px;text-align:center;font-size:10px;color:#555}
.footer nav{margin-top:12px;word-spacing:2px}
.footer nav a{color:#555;text-decoration:none}
</style>
</head>
<body>
<header class="topbar">
  <div class="brand">Velvetfinch</div>
  <div class="social"><span><b>Like</b><i>3k</i></span><span><b>Share</b><i>316</i></span></div>
</header>
<section class="hero">
  <div class="hero-art" role="img" aria-label="Illustration of a frothy mug of golden beer"></div>
  <h1>Velvetfinch is the easiest way to create and share craft beer recipes.</h1>
  <p>In sem eros, gravida sed tincidunt sed, tincidunt vitae nulla. Sed a dolor purus. Mauris imperdiet tellus eu est interdum molestie. Praesent vitae scelerisque massa. Maecenas tincidunt imperdiet elit in euismod. Etiam sit amet sem augue, a dictum ante. Praesent luctus vestibulum blandit. Nunc vestibulum neque ut odio elementum id interdum sem egestas.</p>
</section>
<main class="sheet">
  <div class="search"><span>Stout</span><button>GO</button></div>
  <aside class="panel brewing"><h2>BREWING</h2><ul><li>Extract</li><li>Partial Mash</li><li>All Grain</li></ul></aside>
  <aside class="panel styles"><h2>STYLES</h2><ul><li>American Amber Ale</li><li>American Barleywine</li><li>American Brown Ale</li><li>American IPA</li><li>American Pale Ale</li><li>American Stout</li><li>American Wheat or Rye Beer</li><li>Applewine</li></ul><div class="scroll"><div class="knob"></div></div></aside>
  <aside class="panel match"><h2>MATCH MAKER</h2><ul><li>Boil Size</li></ul></aside>
  <nav class="tabs"><div class="tab active">Recent</div><div class="tab">Popular</div></nav>
  <div class="feedback">Feedback</div>
  <section class="feed">
    <article class="card"><h3>Oak Bastard Sweet Mead</h3><p>Lorem ipsum dolor sit amet, consectetur adipisicing elit, sed do eiusmod tempor incididunt labore et dolore magna aliqua.</p><div class="meta"><div class="by">created by <a href="#">Nora Hale</a></div><span class="tag extract">Extract</span><span class="tag style">Sweet Mead</span></div><div class="stats"><div class="stat"><strong>2.24%</strong><span>abv</span></div><div class="stat"><strong>24</strong><span>ibu</span></div><div class="stat"><strong>1.006</strong><span>fg</span></div><div class="stat"><strong>1.022</strong><span>og</span></div><div class="stat srm"><strong>4</strong><span>srm</span></div></div></article>
    <article class="card"><h3>Oak Bastard Sweet Mead</h3><p>Lorem ipsum dolor sit amet, consectetur adipisicing elit, sed do eiusmod tempor incididunt labore et dolore magna aliqua.</p><div class="meta"><div class="by">created by <a href="#">Nora Hale</a></div><span class="tag mash">Partia Mash</span><span class="tag style">Baltic Porter</span></div><div class="stats"><div class="stat"><strong>2.24%</strong><span>abv</span></div><div class="stat"><strong>24</strong><span>ibu</span></div><div class="stat"><strong>1.006</strong><span>fg</span></div><div class="stat"><strong>1.022</strong><span>og</span></div><div class="stat srm"><strong>4</strong><span>srm</span></div></div></article>
    <article class="card"><h3>Oak Bastard Sweet Mead</h3><p>Lorem ipsum dolor sit amet, consectetur adipisicing elit, sed do eiusmod tempor incididunt labore et dolore magna aliqua.</p><div class="meta"><div class="by">created by <a href="#">Nora Hale</a></div><span class="tag extract">Extract</span><span class="tag style">Sweet Mead</span></div><div class="stats"><div class="stat"><strong>2.24%</strong><span>abv</span></div><div class="stat"><strong>24</strong><span>ibu</span></div><div class="stat"><strong>1.006</strong><span>fg</span></div><div class="stat"><strong>1.022</strong><span>og</span></div><div class="stat srm"><strong>4</strong><span>srm</span></div></div></article>
    <article class="card"><h3>Oak Bastard Sweet Mead</h3><p>Lorem ipsum dolor sit amet, consectetur adipisicing elit, sed do eiusmod tempor incididunt labore et dolore magna aliqua.</p><div class="meta"><div class="by">created by <a href="#">Nora Hale</a></div><span class="tag mash">Partia Mash</span><span class="tag style">Baltic Porter</span></div><div class="stats"><div class="stat"><strong>2.24%</strong><span>abv</span></div><div class="stat"><strong>24</strong><span>ibu</span></div><div class="stat"><strong>1.006</strong><span>fg</span></div><div class="stat"><strong>1.022</strong><span>og</span></div><div class="stat srm"><strong>4</strong><span>srm</span></div></div></article>
    <article class="card"><h3>Oak Bastard Sweet Mead</h3><p>Lorem ipsum dolor sit amet, consectetur adipisicing elit, sed do eiusmod tempor incididunt labore et dolore magna aliqua.</p><div class="meta"><div class="by">created by <a href="#">Nora Hale</a></div><span class="tag extract">Extract</span><span class="tag style">Sweet Mead</span></div><div class="stats"><div class="stat"><strong>2.24%</strong><span>abv</span></div><div class="stat"><strong>24</strong><span>ibu</span></div><div class="stat"><strong>1.006</strong><span>fg</span></div><div class="stat"><strong>1.022</strong><span>og</span></div><div class="stat srm"><strong>4</strong><span>srm</span></div></div></article>
  </section>
</main>
<footer class="footer">
  <div>Copyright &nbsp;© 2013 &nbsp;Velvetfinch, Inc. All third party content © their respective owners.</div>
  <nav><a href="#">Terms of Service</a> &nbsp;| &nbsp;<a href="#">Privacy Policy</a> &nbsp;| &nbsp;<a href="#">Contact</a></nav>
</footer>
</body>
</html>
```